"Thornbury Accupuncture" needs a Promotional Card - A6 size

Requirements
Must have
• Bright colours, pictures of happy people, acupuncture-related pictures.

```html
<!DOCTYPE html>
<html lang="en">
<head>
<meta charset="utf-8">
<title>Thornbury Acupuncture – Promotional Cards</title>
<link rel="stylesheet" href="https://fonts.googleapis.com/css2?family=Source+Sans+3:wght@400;600;700&display=swap">
<style>
  :root {
    --bg: #ecebe8;
    --paper: #ffffff;
    --gold: #e2c26f;
    --gold-deep: #cfa94a;
    --gold-light: #f1dc9f;
    --red: #e1402b;
    --ink: #4a4a4a;
    --ink-soft: #5c5c5c;
    --skin: #e9d6c7;
    --skin-deep: #d9b9a1;
    --leaf: #a9b98c;
  }
  * { box-sizing: border-box; margin: 0; padding: 0; }
  html, body { width: 1200px; height: 912px; overflow: hidden; }
  body {
    background: var(--bg);
    font-family: "Source Sans 3", sans-serif;
    color: var(--ink);
    position: relative;
  }
  .card {
    position: absolute;
    width: 497px;
    height: 703px;
    background: var(--paper);
    box-shadow: 0 2px 6px rgba(0,0,0,.18);
    overflow: hidden;
  }
  .card--front { left: 90px; top: 87px; }
  .card--back { left: 628px; top: 123px; }
  .photo { position: absolute; }
  .wave { position: absolute; left: 0; width: 100%; }
  .footer-band {
    position: absolute; left: 0; bottom: 0; width: 100%; height: 12px;
    background: var(--gold);
  }
  .social-dot {
    position: absolute; left: 18px; top: 18px; width: 40px; height: 40px;
    border-radius: 50%; background: var(--red);
  }
  .brand-name {
    position: absolute;
    color: var(--red);
    font-weight: 700;
    font-size: 27px;
    line-height: 25px;
    text-align: center;
    letter-spacing: .3px;
  }
  .front-lead {
    position: absolute; left: 0; top: 436px; width: 100%;
    text-align: center; font-size: 18.5px; line-height: 25px; color: var(--ink-soft);
  }
  .front-body {
    position: absolute; left: 0; top: 512px; width: 100%;
    text-align: center; font-size: 15px; line-height: 19px; color: var(--ink-soft);
  }
  .call {
    position: absolute; font-size: 18px; line-height: 24px; color: var(--ink);
  }
  .call .phone { color: var(--red); font-weight: 700; }
  .call svg { vertical-align: -2px; margin: 0 3px 0 4px; }
  .front-call { left: 22px; top: 628px; }
  .intro {
    position: absolute; left: 22px; top: 346px; width: 452px;
    font-size: 9.6px; line-height: 11.6px; color: var(--ink);
  }
  .works-title {
    position: absolute; left: 22px; top: 428px;
    font-size: 16.5px; color: var(--gold-deep); font-weight: 400; letter-spacing: .2px;
  }
  .works-list {
    position: absolute; left: 22px; top: 453px; list-style: none;
    font-size: 15px; line-height: 23.5px; color: var(--ink);
  }
  .works-list li::before {
    content: "›";
    display: inline-block; width: 12px; height: 12px; margin-right: 6px;
    border-radius: 50%; background: var(--gold);
    color: #fff; font-size: 12px; line-height: 11px; text-align: center;
    font-weight: 700; vertical-align: 0;
  }
  .practitioner {
    position: absolute; left: 116px; top: 598px;
    font-size: 14.5px; line-height: 18.5px; color: var(--gold-deep);
  }
  .back-call { left: 116px; top: 642px; font-size: 13.5px; line-height: 18px; }
</style>
</head>
<body>

<!-- Front card -->
<section class="card card--front">
  <div class="photo" role="img" aria-label="Practitioner's hand placing acupuncture needles in a relaxed patient's forehead"
       style="left:0;top:0;width:497px;height:360px;background:linear-gradient(160deg,#f5eee9 0%,var(--skin) 45%,#f4ece6 100%);"></div>
  <span class="social-dot" aria-hidden="true"></span>
  <svg class="wave" style="top:285px" width="497" height="110" viewBox="0 0 497 110" aria-hidden="true">
    <path d="M0 20 C120 70 200 75 290 50 C380 25 440 30 497 45 L497 110 L0 110 Z" fill="#fff"/>
    <path d="M0 30 C110 80 210 92 300 70 C390 48 450 50 497 60 L497 80 C440 70 380 72 300 92 C210 110 110 100 0 70 Z" fill="var(--gold)"/>
    <path d="M0 45 C140 20 240 30 330 60 C400 82 460 84 497 78" fill="none" stroke="var(--gold-light)" stroke-width="2"/>
    <path d="M0 60 C130 40 230 55 320 78 C400 96 460 96 497 90" fill="none" stroke="var(--gold-deep)" stroke-width="1.2"/>
  </svg>
  <p class="front-lead">Acupuncture improves the well-being and<br>contribute to physical and emotional balance.</p>
  <p class="front-body">Come recive a stress reducing<br>Acupuncture treatment from<br>Mirela Kostova, Thornbury Acupuncture</p>
  <p class="call front-call">Call<svg width="16" height="16" viewBox="0 0 16 16" aria-hidden="true"><circle cx="8" cy="8" r="7" fill="none" stroke="var(--red)" stroke-width="1.5"/><path d="M5.2 4.3l1.3-.3.8 1.8-.9.7c.5 1 1.2 1.7 2.2 2.2l.7-.9 1.8.8-.3 1.3c-2.9.2-5.8-2.7-5.6-5.6z" fill="var(--red)"/></svg><span class="phone">07700 900123</span><br>to book your appointment</p>
  <p class="brand-name" style="left:270px;top:612px;width:210px;">thornbury<br>acupuncture</p>
  <div class="footer-band"></div>
</section>

<!-- Back card -->
<section class="card card--back">
  <div class="photo" role="img" aria-label="Happy three-generation family laughing together on a sofa in a sunny garden"
       style="left:0;top:0;width:497px;height:300px;background:linear-gradient(180deg,#c9d2a8 0%,var(--leaf) 25%,#e8cfc0 60%,#d8c2b0 100%);"></div>
  <svg class="wave" style="top:160px" width="497" height="150" viewBox="0 0 497 150" aria-hidden="true">
    <path d="M0 95 C120 40 260 20 360 30 C420 36 465 40 497 35 L497 150 L0 150 Z" fill="var(--gold)"/>
    <path d="M0 110 C130 60 260 45 360 55 C420 60 465 62 497 58 L497 150 L0 150 Z" fill="#fff"/>
  </svg>
  <p class="brand-name" style="left:270px;top:252px;width:210px;">thornbury<br>acupuncture</p>
  <p class="intro">The term “acupuncture” describes a family of procedures involving the stimulation of points on the body using a variety of techniques. The acupuncture technique that has been most often studied scientifically involves penetrating the skin with thin, solid, metallic needles that are manipulated by the hands or by electrical stimulation.</p>
  <h2 class="works-title">HOW ACUPUNCURE WORKS</h2>
  <ul class="works-list">
    <li>Releases Endorphins</li>
    <li>Balancing Neurotransmitters</li>
    <li>Regulates Immune System</li>
    <li>Improving Circulatio</li>
  </ul>
  <div class="photo" role="img" aria-label="Woman relaxing during a facial acupuncture treatment"
       style="left:350px;top:415px;width:121px;height:82px;background:linear-gradient(135deg,#f3e6dc,var(--skin-deep));"></div>
  <div class="photo" role="img" aria-label="Needles being placed along a patient's back"
       style="left:350px;top:505px;width:121px;height:82px;background:linear-gradient(135deg,#f6e2d6,#dea58f);"></div>
  <div class="photo" role="img" aria-label="Woman lying face down receiving a relaxing back treatment"
       style="left:350px;top:593px;width:121px;height:82px;background:linear-gradient(135deg,#efe1d6,#c99a80);"></div>
  <div class="photo" role="img" aria-label="Portrait of the practitioner"
       style="left:18px;top:582px;width:88px;height:106px;background:linear-gradient(180deg,#f2ece8 0%,#b89a8a 55%,#8a5f7a 100%);"></div>
  <p class="practitioner">Mirela Kostova<br>Thornbury Acupuncture</p>
  <p class="call back-call">Call<svg width="13" height="13" viewBox="0 0 16 16" aria-hidden="true"><circle cx="8" cy="8" r="7" fill="none" stroke="var(--red)" stroke-width="1.5"/><path d="M5.2 4.3l1.3-.3.8 1.8-.9.7c.5 1 1.2 1.7 2.2 2.2l.7-.9 1.8.8-.3 1.3c-2.9.2-5.8-2.7-5.6-5.6z" fill="var(--red)"/></svg><span class="phone">07700 900123</span><br>to book your appointment</p>
  <div class="footer-band"></div>
</section>

</body>
</html>
```